Adelaide based cleaning and remediation business needs a website design

We are launching a new company with no clients as yet so we don't have the benefit of Plimora Reviews to build confidence. We can use our  past work history with other employers in the industry to give some credibility. Happy to use any colour scheme as long as it look interesting when people click on the site it gets there attention. enquiry . I have supplied a mock up the important information and various photos as they tell a lot of the story.

```html
<!DOCTYPE html>
<html lang="en">
<head>
<meta charset="utf-8">
<title>Kalora Services Pty Ltd</title>
<link href="https://fonts.googleapis.com/css2?family=Lato:wght@400;700;900&display=swap" rel="stylesheet">
<style>
:root{
  --blue:#2783c4;
  --blue-deep:#1e5f92;
  --orange:#fbb02a;
  --ink:#1d1d1d;
  --muted:#4a4a4a;
  --grey:#f1f1f1;
  --ghost:#e3e3e3;
  --white:#ffffff;
  --dark:#232323;
}
*{box-sizing:border-box;margin:0;padding:0}
html,body{width:1200px;height:3969px;overflow:hidden}
body{font-family:'Lato',sans-serif;color:var(--ink);background:var(--white);position:relative}
.abs{position:absolute}
.nav{top:0;left:0;width:1200px;height:57px;background:var(--white);z-index:5}
.nav-links{position:absolute;left:505px;top:22px;display:flex;gap:22px;font-size:12px;font-weight:700;letter-spacing:.2px}
.nav-links .active{color:var(--orange);border-bottom:3px solid var(--orange);padding-bottom:16px}
.logo-box{left:151px;top:0;width:111px;height:140px;background:var(--white);border:1px solid #999;z-index:6;display:flex;align-items:center;justify-content:center;font-size:15px;font-weight:900;color:var(--ink)}
.hero{top:57px;left:0;width:1200px;height:640px;background:linear-gradient(135deg,#1f5f8f,#2c7fbd 55%,#2272ad)}
.scroll-tag{left:68px;top:350px;transform:rotate(90deg);color:var(--white);font-size:13px}
.hero-title{left:130px;top:262px;width:500px;text-align:center;color:var(--white)}
.hero-title h1{font-size:92px;font-weight:900;letter-spacing:1px;line-height:1}
.hero-title p{font-size:45px;font-weight:700;margin-top:8px}
.btn{position:absolute;border-radius:24px;font-size:12px;font-weight:700;display:flex;align-items:center;justify-content:center}
.btn-orange{background:var(--orange);color:var(--ink)}
.btn-white{background:var(--white);color:var(--ink)}
.hero-ring{left:598px;top:140px;width:450px;height:450px;border-radius:50%;background:rgba(255,255,255,.18)}
.photo{background:linear-gradient(135deg,#6a7f96,#3b4a5a)}
.hero-photo{left:614px;top:153px;width:416px;height:416px;border-radius:50%;background:linear-gradient(135deg,#8aa7c4,#2f5d9a 50%,#4a3e38)}
.section-head{left:0;width:1200px;text-align:center}
.section-head .ghost{font-size:64px;font-weight:700;color:var(--ghost);white-space:nowrap;line-height:1}
.section-head h2{position:absolute;left:0;right:0;top:12px;font-size:36px;font-weight:700;color:var(--ink)}
.tabs{left:245px;top:856px;display:flex;align-items:center;gap:8px;font-size:13px;font-weight:700}
.tab-active{background:var(--orange);color:var(--white);padding:6px 10px;border-radius:4px;position:relative}
.tab-active::after{content:"";position:absolute;left:100px;bottom:-7px;border:7px solid transparent;border-bottom:0;border-top-color:var(--orange)}
.circ{border-radius:50%;border:6px solid var(--white);box-shadow:0 6px 14px rgba(0,0,0,.18)}
.arrow{font-size:34px;color:var(--ink);font-weight:400}
.band-grey{left:0;width:1200px;background:var(--grey)}
.card{position:absolute;background:var(--white);border-radius:10px;box-shadow:0 2px 6px rgba(0,0,0,.05)}
.card h3{font-size:24px;font-weight:700;position:absolute;left:18px}
.card .tog{position:absolute;right:36px;font-size:22px;font-weight:700}
.card p,.card li{font-size:12.5px;color:var(--muted);line-height:1.5}
.card ul{list-style:none;position:absolute;left:18px;right:20px}
.card li{position:relative;padding-left:22px;margin-bottom:14px;font-size:11px}
.card li::before{content:"";position:absolute;left:0;top:4px;width:9px;height:9px;border-radius:50%;background:var(--orange)}
.blob{border-radius:70px 40px 120px 40px;transform:rotate(-4deg)}
.quote{left:507px;top:2300px;width:420px}
.quote .mark{font-size:30px;font-weight:900;line-height:1}
.quote p{font-size:13.5px;color:var(--muted);line-height:1.3;margin-top:10px}
.quote h4{font-size:19px;font-weight:700;margin-top:18px;color:#333}
.faq h3{font-size:19px;font-weight:700;text-transform:uppercase}
.footer-text{color:var(--white)}
.footer-text h3{font-size:31px;font-weight:700}
.footer-text .row{display:flex;gap:8px;align-items:flex-start;font-size:14px;margin-top:16px;line-height:1.25}
.icon{width:16px;height:16px;flex:none;margin-top:1px}
.input{left:491px;top:3758px;width:358px;height:33px;border:1px solid rgba(255,255,255,.8);border-radius:6px;color:rgba(255,255,255,.6);font-size:13px;padding:8px 12px}
.badge{left:890px;top:3684px;width:154px;height:71px;background:var(--white);border-radius:6px;display:flex;align-items:center;justify-content:center}
.bottom{left:0;top:3899px;width:1200px;height:70px;background:var(--dark);color:var(--white)}
.pay{width:28px;height:20px;background:#e8e8e8;border-radius:3px}
</style>
</head>
<body>

<header class="abs nav">
  <nav class="nav-links">
    <span class="active">HOME</span><span>ABOUT US</span><span>SERVICES</span><span>WHAT WE DO</span><span>TESTIMONIALS</span><span>CONTACT US</span>
  </nav>
</header>
<div class="abs logo-box">KALORA</div>

<section class="abs hero" role="img" aria-label="Blue tinted photo of a cleaning site"></section>
<div class="abs hero-ring"></div>
<div class="abs hero-photo" role="img" aria-label="Operative in protective suit and respirator sorting debris"></div>
<svg class="abs" style="left:0;top:480px" width="1200" height="240" viewBox="0 480 1200 240">
  <path d="M0,640 C320,700 560,530 880,535 C1030,538 1130,520 1200,505 L1200,720 L0,720 Z" fill="var(--orange)"/>
  <path d="M0,650 C330,705 620,585 900,592 C1050,596 1140,640 1200,625 L1200,720 L0,720 Z" fill="var(--white)"/>
</svg>
<div class="abs scroll-tag">scroll →</div>
<div class="abs hero-title">
  <h1>KALORA</h1>
  <p>SERVICES PTY LTD</p>
</div>
<div class="btn btn-orange" style="left:199px;top:450px;width:173px;height:43px">DIRTY JOB CLEANERS</div>
<div class="btn btn-white" style="left:380px;top:450px;width:133px;height:43px">GET A QUOTE</div>

<div class="abs section-head" style="top:770px">
  <div class="ghost">OUR SIGNATURE SERVICES</div>
  <h2>OUR SIGNATURE SERVICES</h2>
</div>
<div class="abs tabs">
  <span class="tab-active">End of lease &amp; estate Clean ups</span>|<span>Squalor Clean ups</span>|<span>Pigeon Waste Clean Ups</span>|<span>Fire Damage Clean Outs</span>
</div>
<div class="abs arrow" style="left:92px;top:1102px">&#8249;</div>
<div class="abs arrow" style="left:1073px;top:1102px">&#8250;</div>
<div class="abs circ" style="left:160px;top:968px;width:310px;height:310px;background:linear-gradient(135deg,#c9a56a,#6b4a34)" role="img" aria-label="Cluttered storeroom shelves"></div>
<div class="abs circ" style="left:740px;top:968px;width:300px;height:310px;background:linear-gradient(135deg,#8b6a52,#5a7a48)" role="img" aria-label="Rusted scrap and bicycle in a yard"></div>
<div class="abs circ" style="left:415px;top:950px;width:372px;height:372px;background:linear-gradient(135deg,#b3aca3,#5d4f43)" role="img" aria-label="Hoarded household items and baskets"></div>

<section class="abs band-grey" style="top:1394px;height:667px"></section>
<div class="abs section-head" style="top:1445px">
  <div class="ghost">WE DO THE STUFF NOBODY WANTS TO DO</div>
  <h2>WE DO THE STUFF NOBODY WANTS TO DO</h2>
</div>
<div class="abs blob" style="left:146px;top:1535px;width:430px;height:440px;background:linear-gradient(160deg,#eeeeea,#b2a78f 70%,#6c5a44)" role="img" aria-label="Pigeons on a ledge above a stained wall"></div>

<div class="card" style="left:613px;top:1543px;width:450px;height:271px">
  <h3 style="top:16px">PIGEON WASTE</h3><span class="tog" style="top:10px">–</span>
  <div style="position:absolute;left:18px;right:18px;top:56px;border-top:1px dashed #ddd"></div>
  <p style="position:absolute;left:18px;right:40px;top:68px">Can cause damage to buildings and spread disease, mites and bacteria, triggering alarms and damaging the reputation of businesses.</p>
  <ul style="top:140px">
    <li>The pigeon faeces is carefully removed by our trained operatives, who also dispose of it in an environmentally friendly way.</li>
    <li>Next, in order to remove stains and ensure safety, we use eco-friendly chemicals to clean and disinfect the impacted areas.</li>
    <li>We advise adding anti-nesting spikes as an option.</li>
  </ul>
</div>
<div class="card" style="left:613px;top:1831px;width:450px;height:54px"><h3 style="top:12px">FIRE DAMAGE CLEAN OUTS</h3><span class="tog" style="top:12px">+</span></div>
<div class="card" style="left:613px;top:1903px;width:450px;height:56px"><h3 style="top:13px">SQULAOR ESTATE CLEAN UPS</h3><span class="tog" style="top:12px">+</span></div>

<div class="abs section-head" style="top:2150px">
  <div class="ghost">ONLY THE BEST SERVICE FOR OUR CUSTOMERS</div>
  <h2>ONLY THE BEST SERVICE FOR OUR CUSTOMERS</h2>
</div>
<div class="abs arrow" style="left:180px;top:2358px">&#8249;</div>
<div class="abs arrow" style="left:983px;top:2364px">&#8250;</div>
<div class="abs" style="left:257px;top:2282px;width:210px;height:210px;border-radius:50%;background:linear-gradient(135deg,#6f7257,#2f3228)" role="img" aria-label="Pile of discarded waste being cleared"></div>
<div class="abs quote">
  <div class="mark">&#8220;&#8220;</div>
  <p>Daniel and his team arrived the next morning to clean up a rental property my husband and I own which and had been trashed by the tenants. He was the only contractor to return my call. They did an amazing job and also deodorised the house for no extra charge.</p>
  <h4>Marianne Holt, Satisfied customer</h4>
</div>

<section class="abs band-grey" style="top:2581px;height:700px"></section>
<div class="abs section-head" style="top:2636px">
  <div class="ghost">FREQUENTLY ASKED QUESTIONS</div>
  <h2>FREQUENTLY ASKED QUESTIONS</h2>
</div>
<div class="card faq" style="left:140px;top:2753px;width:439px;height:265px">
  <h3 style="position:absolute;left:22px;top:22px">What we are doing ?</h3><span class="tog" style="top:18px;right:22px;font-size:18px">&#8964;</span>
  <p style="position:absolute;left:26px;right:40px;top:64px;font-size:13px;line-height:1.85">Adelaide-based Kalora Services is a family-run organisation. We have been in operation for more than two decades. We've gained some knowledge about cleaning and squalor removal services throughout the years. As a small South Australian company, we base everything on responsibility honesty and fairness. We are aware of the confidence you put in us when you seek our help.</p>
</div>
<div class="card faq" style="left:140px;top:3034px;width:439px;height:51px"><h3 style="position:absolute;left:22px;top:15px">Pricing ?</h3><span class="tog" style="top:11px;right:26px">&#8250;</span></div>
<div class="card faq" style="left:140px;top:3098px;width:439px;height:51px"><h3 style="position:absolute;left:22px;top:15px">Qualifications ?</h3><span class="tog" style="top:11px;right:26px">&#8250;</span></div>
<div class="abs blob" style="left:608px;top:2735px;width:435px;height:445px;background:linear-gradient(150deg,#9a9690,#4b4037 60%,#2a2420)" role="img" aria-label="Fire damaged shed with burnt shelving"></div>

<svg class="abs" style="left:0;top:3190px" width="1200" height="710" viewBox="0 3190 1200 710">
  <path d="M0,3300 C420,3250 820,3290 1200,3200 L1200,3900 L0,3900 Z" fill="var(--orange)"/>
  <path d="M0,3312 C360,3270 760,3340 1200,3252 L1200,3900 L0,3900 Z" fill="var(--blue)"/>
</svg>

<div class="abs" style="left:180px;top:3400px;width:108px;height:116px;background:rgba(255,255,255,.9);display:flex;align-items:center;justify-content:center;font-weight:900;font-size:16px;color:var(--ink)">KALORA</div>

<div class="abs footer-text" style="left:177px;top:3535px;width:290px">
  <h3>Contact Us</h3>
  <div class="row"><svg class="icon" viewBox="0 0 16 16"><path d="M8 1a5 5 0 0 0-5 5c0 4 5 9 5 9s5-5 5-9a5 5 0 0 0-5-5zm0 7a2 2 0 1 1 0-4 2 2 0 0 1 0 4z" fill="#fff"/></svg><span>14 Wendale Road Parkholme<br>SA5092</span></div>
  <div class="row"><svg class="icon" viewBox="0 0 16 16"><path d="M3 1l3 0 1 4-2 1c1 2 3 4 5 5l1-2 4 1v3c0 1-1 2-2 2C7 15 1 9 1 3c0-1 1-2 2-2z" fill="#fff"/></svg><span>Daniel or Tarek 0400 555 017</span></div>
  <div class="row" style="margin-top:22px"><svg class="icon" viewBox="0 0 16 16"><rect x="1" y="3" width="14" height="10" rx="1" fill="#fff"/><path d="M1 4l7 5 7-5" stroke="var(--blue)" fill="none"/></svg><span>admin@kaloraservices.example</span></div>
  <div class="row" style="margin-top:10px;display:block">Got more questions about our clean-up services and what we offer?<br><b>Get in touch today</b></div>
  <div class="row"><svg class="icon" viewBox="0 0 16 16"><rect x="4" y="1" width="8" height="14" rx="1.5" fill="none" stroke="#fff" stroke-width="1.6"/></svg><span>0400 555 017</span></div>
</div>

<div class="abs footer-text" style="left:493px;top:3535px;width:380px">
  <h3>Business Hours</h3>
  <div class="row"><svg class="icon" viewBox="0 0 16 16"><circle cx="8" cy="8" r="7" fill="#fff"/><path d="M8 4v4l3 2" stroke="var(--blue)" stroke-width="1.6" fill="none"/></svg><span>Monday to Saturday<br>8:00 am to 4:00 pm</span></div>
  <h3 style="margin-top:32px">Get a quickQuote</h3>
  <div class="row" style="display:block;margin-top:6px;font-size:13.5px">Send a text to Kalora Services<br>Please enter your mobile number or email and message</div>
</div>
<div class="abs input">0400555017</div>
<div class="btn btn-orange" style="left:491px;top:3810px;width:310px;height:37px;font-size:13px">MESSAGE and any attachements</div>

<div class="abs footer-text" style="left:886px;top:3535px;width:260px">
  <h3>Follow Us</h3>
  <div class="row"><svg class="icon" viewBox="0 0 16 16"><circle cx="8" cy="8" r="7" fill="#fff"/></svg><span>Chatterbook</span></div>
  <div class="row"><svg class="icon" viewBox="0 0 16 16"><rect x="1.5" y="1.5" width="13" height="13" rx="3" fill="none" stroke="#fff" stroke-width="1.6"/></svg><span>Snapgram</span></div>
</div>
<div class="abs badge"><div style="width:110px;height:44px;border-radius:6px;background:#d9ead3"></div></div>

<footer class="abs bottom">
  <div class="abs" style="left:162px;top:22px;font-size:22px;font-weight:700">We accept all major credit cards</div>
  <div class="abs" style="left:522px;top:25px;display:flex;gap:16px">
    <div class="pay"></div><div class="pay"></div><div class="pay"></div><div class="pay"></div><div class="pay"></div><div class="pay"></div>
  </div>
  <div class="abs" style="left:930px;top:28px;font-size:11px">© 2025 | www.kalora.example</div>
  <div class="abs" style="left:1084px;top:28px;font-size:11px">M1</div>
</footer>

</body>
</html>
```